An image to show that our fees are offset by our good management

We work in the property sector.
We'd like a slide showing that our fees weigh very little compared with the savings we can generate if we do our job properly as property managers.
To do this, we've come up with a slide with a scale showing our fees on the left (which weigh less or the same) than the items on the right.
On the right you can see:
Savings on building maintenance costs
Savings on running costs
Optimization of vacant periods
Good monitoring of disputes to avoid rental losses
We welcome any other ideas you may have to highlight this concept (even off-balance sheet).

```html
<!DOCTYPE html>
<html lang="en">
<head>
<meta charset="utf-8">
<title>Off-Balance Sheet of Our Fees &amp; Our Good Management</title>
<link rel="stylesheet" href="https://fonts.googleapis.com/css2?family=Poppins:wght@600;700;800&display=swap">
<style>
  :root {
    --ink: #2a2727;
    --paper: #f3f3f2;
    --green: #7cc04b;
    --green-line: #86c44f;
    --white: #ffffff;
    --red: #df5a59;
    --blue: #3e84e6;
    --teal: #16a985;
    --orange: #fb9b07;
    --plank-dark: #9a6434;
    --plank-light: #c88d57;
    --text-dark: #1d1d1d;
  }
  * { box-sizing: border-box; margin: 0; padding: 0; }
  html, body { width: 1200px; height: 901px; overflow: hidden; background: var(--paper); }
  body { font-family: "Poppins", sans-serif; }

  .slide { position: relative; width: 1200px; height: 901px; background: var(--paper); overflow: hidden; }

  .header { position: absolute; left: 0; top: 0; width: 1200px; height: 225px; background: var(--ink); }
  .title {
    position: absolute; left: 0; width: 1200px; top: 52px; text-align: center;
    font-weight: 700; font-size: 101px; line-height: 1; letter-spacing: 1px; color: var(--green);
  }
  .subtitle {
    position: absolute; left: 0; width: 1200px; top: 147px; text-align: center;
    font-weight: 700; font-size: 45px; line-height: 1; color: var(--white);
  }
  .header-rule { position: absolute; left: 67px; top: 218px; width: 1069px; height: 10px; background: var(--green-line); }

  .fees-visual {
    position: absolute; left: 108px; top: 270px; width: 350px; height: 370px;
    border-radius: 14px;
    background: linear-gradient(160deg, #b9c3ae 0%, #8ccf5e 45%, #c9a253 100%);
  }

  .benefit {
    position: absolute; left: 480px; width: 650px; border-radius: 30px;
    color: var(--white); font-weight: 700; font-size: 21.5px; line-height: 1.18;
    padding-left: 27px; display: flex; align-items: center;
  }
  .benefit--maintenance { top: 270px; height: 66px; background: var(--red); }
  .benefit--running { top: 348px; height: 66px; background: var(--blue); }
  .benefit--vacancy { top: 436px; height: 66px; background: var(--teal); }
  .benefit--disputes { top: 538px; height: 84px; background: var(--orange); }

  .benefit-icon { position: absolute; right: 22px; top: 50%; transform: translateY(-50%); width: 50px; height: 50px; }

  .stones-visual {
    position: absolute; left: 735px; top: 263px; width: 325px; height: 378px;
    border-radius: 45% 45% 30% 30% / 30% 30% 22% 22%;
    background: linear-gradient(180deg, #2b2b2b 0%, #1a1a1a 100%);
  }

  .plank {
    position: absolute; left: 81px; top: 638px; width: 1049px; height: 24px;
    background: linear-gradient(90deg, var(--plank-dark), var(--plank-light) 50%, var(--plank-dark));
  }

  .caption {
    position: absolute; top: 726px; height: 66px; border: 2px solid var(--green);
    border-radius: 14px; background: var(--white); color: var(--text-dark);
    font-weight: 600; font-size: 21px; line-height: 1.2; display: flex; align-items: center;
  }
  .caption--fees { left: 90px; width: 420px; padding-left: 28px; }
  .caption--savings { left: 720px; width: 414px; padding-left: 46px; }

  .pivot-visual {
    position: absolute; left: 433px; top: 665px; width: 302px; height: 146px;
    border-radius: 50%;
    background: radial-gradient(ellipse at 45% 40%, #c9c9c7 0%, #9c9c9a 70%, #6f6f6d 100%);
  }
  .pivot-label {
    position: absolute; left: 433px; top: 710px; width: 302px; text-align: center;
    font-weight: 800; font-size: 27px; line-height: 1.05; letter-spacing: 1px; color: #4a4a48;
  }
</style>
</head>
<body>
<main class="slide">
  <header class="header">
    <h1 class="title">OFF-BALANCE SHEET</h1>
    <p class="subtitle">OF OUR FEES &amp; OUR GOOD MANAGEMENT</p>
  </header>
  <div class="header-rule"></div>

  <div class="fees-visual" role="img" aria-label="Jar of banknotes labelled FEES with stacks of gold coins and a large green dollar sign"></div>

  <div class="benefit benefit--maintenance">Savings On Building<br>Maintenance Costs
    <svg class="benefit-icon" viewBox="0 0 50 50" fill="none" stroke="#1d1d1d" stroke-width="2.2">
      <circle cx="14" cy="32" r="9" fill="#fff"/><text x="14" y="37" text-anchor="middle" font-size="13" font-weight="700" fill="#1d1d1d" stroke="none">$</text>
      <rect x="28" y="34" width="4" height="10" fill="#fff"/><rect x="35" y="28" width="4" height="16" fill="#fff"/><rect x="42" y="22" width="4" height="22" fill="#fff"/>
      <circle cx="36" cy="10" r="5" fill="#fff"/>
    </svg>
  </div>
  <div class="benefit benefit--running">Savings On<br>Running Costs
    <svg class="benefit-icon" viewBox="0 0 50 50" fill="none" stroke="#1d1d1d" stroke-width="2.2">
      <rect x="10" y="4" width="36" height="16" rx="2" fill="#fff"/><circle cx="28" cy="12" r="4"/>
      <rect x="3" y="22" width="20" height="24" rx="2" fill="#fff"/><path d="M7 34h4M13 34h4M7 40h4M13 40h4M7 27h12"/>
      <circle cx="36" cy="36" r="9" fill="#fff"/><text x="36" y="41" text-anchor="middle" font-size="12" font-weight="700" fill="#1d1d1d" stroke="none">$</text>
    </svg>
  </div>
  <div class="benefit benefit--vacancy">Optimization Of<br>Vacant Periods
    <svg class="benefit-icon" viewBox="0 0 50 50" fill="none" stroke="#1d1d1d" stroke-width="2.2">
      <rect x="16" y="3" width="18" height="18" rx="2" fill="#fff"/><text x="25" y="17" text-anchor="middle" font-size="13" font-weight="700" fill="#1d1d1d" stroke="none">?</text>
      <path d="M5 28h40M12 28v6h26v-6M25 34v8M16 46l9-4 9 4"/>
    </svg>
  </div>
  <div class="benefit benefit--disputes">Good Monitoring<br>of Disputes to Avoid<br>Rental Losses
    <svg class="benefit-icon" viewBox="0 0 50 50" fill="none" stroke="#1d1d1d" stroke-width="2.2">
      <circle cx="10" cy="12" r="8" fill="#fff"/><circle cx="40" cy="12" r="8" fill="#fff"/><circle cx="25" cy="20" r="8" fill="#fff"/>
      <path d="M10 22v14M7 33l3 3 3-3M40 22v14M37 33l3 3 3-3M25 30v16M22 43l3 3 3-3"/>
    </svg>
  </div>

  <div class="stones-visual" role="img" aria-label="Stack of four smooth black stones resting on the scale"></div>

  <div class="plank"></div>

  <p class="caption caption--fees">Our fees weigh very little</p>
  <p class="caption caption--savings">The savings we can generate<br>if we do our job</p>

  <div class="pivot-visual" role="img" aria-label="Grey pebble acting as the scale's pivot"></div>
  <p class="pivot-label">COMPARED<br>WITH</p>
</main>
</body>
</html>
```